High-end Oceanfront Real Estate Group Needs Clean, Modern Web Design

I’m looking for a clean, professional, modern and beautiful homepage web design for a Real Estate group in Southern California, USA.

The group/company is “Marwick on the Shore,” and they specialize in high end (i.e. expensive), oceanfront real estate in the Orange County area.

The look and feel of the page should accentuate the brand qualities: luxurious/expensive, professional, and beautiful (Orange County is one of the most beautiful areas in all the US and we would love the site to emphasize the beautiful beaches and scenery it has to offer).

Looks we like:
• www.brantleyhomesrealty.example
• www.closedbyvane.example -- I think the design is pretty out-dated in this site, but I like the organization/layout of the site

Header Tags (I don’t know if we can fit all of these, may need a side-menu, but I’d prefer header title only if possible):
• Welcome
• Featured Listings
• Previously Sold
• Sell
• Property Search
• Team
• Videos
• Blog
• Explore O.C.
• Contact

I have attached the beach and logo pics that we would like to use as the header, a few pictures of the team, and one sample home/view pic which can be used in any of the other sections (for pictures of the homes, just find expensive oceanfront houses and that will be fine).

I promise to provide feedback to each and every design submission. I appreciate the hard work that all of you are putting into your designs. There can be only one contest winner, but I hope to give all of you helpful feedback to submit the best designs possible!

Target Market(s)

Very wealthy home owners of oceanfront properties. These properties are worth several millions of dollars, and thus the site and brand needs to be targeted to very wealthy, successful individuals and families (both US and international buyers).

Industry/Entity Type

Real Estate

Number of Pages Required

2 page

Requirements
Must have
• I don’t want to give too many requirements, because I want to let you all be creative. However, here are the few Must Haves:
• Must submit 2 page designs (a home page and a sub page)
• Must use logo provided
• Focus is mostly on homes, but I would like to include some beach/ocean imagery as well
• The first “item” on the home page should be an accordion/slider which shows pictures of homes and with 1 line of text: “List with the Leader” and two link buttons: “Sell Your Home” and “Buy Your Home”
• Color palette needs to be mainly blues--to match ocean and sky blue
• Exported in all major formats (psd,ai,eps,png,jpeg,etc)
Nice to have
• We don’t necessarily need all of these, but would like to feature most:
• List of videos
• “Meet the Team”—brief team bios and pics
• Link(s) to Blog
• “List with the Leader” – section on why they should choose this firm
• Featured Listings
• Previously Sold

```html
<!DOCTYPE html>
<html lang="en">
<head>
<meta charset="utf-8">
<title>Marwick on the Shore — Oceanfront Real Estate</title>
<link rel="stylesheet" href="https://fonts.googleapis.com/css2?family=Open+Sans:wght@400;600;700&family=Oswald:wght@400;500&display=swap">
<style>
:root{
  --blue:#1a73c9;
  --blue-dark:#0f5aa3;
  --navy:#142033;
  --ink:#2b2b2b;
  --muted:#6b6b6b;
  --line:#d9d9d9;
  --grey-band:#ececec;
  --footer:#161616;
  --footer-deep:#0b0b0b;
  --white:#ffffff;
  --mail-grey:#7a7a7a;
}
*{box-sizing:border-box;margin:0;padding:0}
html,body{width:1200px;height:3821px;overflow:hidden}
body{font-family:"Open Sans",Arial,sans-serif;color:var(--ink);background:var(--white);font-size:13px;position:relative}
.section{position:absolute;left:0;width:1200px}
.center{text-align:center}
.btn-blue{display:inline-block;background:var(--blue);color:var(--white);font-weight:700;font-size:14px;text-align:center}

/* Hero */
.hero{top:0;height:597px;background:linear-gradient(180deg,#8fb6d8 0%,#b7cfe0 30%,#6f8f4a 62%,#4d7030 100%)}
.hero-photo{position:absolute;inset:0}
.brand{position:absolute;left:130px;top:0;width:140px;height:108px;background:rgba(255,255,255,.22);border:1px solid rgba(255,255,255,.6);display:flex;align-items:center;justify-content:center;text-align:center;color:var(--white);font-weight:600;font-size:19px;line-height:1.2;padding:8px}
.topbar{position:absolute;right:130px;top:14px;display:flex;gap:8px;align-items:center}
.social{width:24px;height:24px;border-radius:50%;border:2px solid var(--white)}
.lang{margin-left:8px;border:1px solid var(--white);border-radius:12px;color:var(--white);font-size:11px;padding:3px 12px}
.nav{position:absolute;left:330px;top:62px;display:flex;font-size:13px;color:var(--white);font-weight:600}
.nav a{padding:12px 17px;color:var(--white);text-decoration:none}
.nav a.active{background:rgba(255,255,255,.85);color:var(--blue)}
.hero-title{position:absolute;top:398px;left:0;width:100%;text-align:center;font-family:"Oswald",sans-serif;font-size:38px;color:var(--white);letter-spacing:.5px;text-shadow:0 2px 6px rgba(0,0,0,.5)}
.hero-actions{position:absolute;top:495px;left:0;width:100%;display:flex;justify-content:center;gap:36px}
.hero-btn{width:300px;height:60px;background:rgba(20,20,20,.75);border-radius:6px;display:flex;align-items:center;justify-content:center;gap:14px;font-family:"Oswald",sans-serif;font-size:26px;color:var(--white)}
.hero-btn svg{width:30px;height:30px}

/* Search */
.search{top:597px;height:173px;background:#f5f5f5;border-bottom:1px solid var(--line)}
.search h2{position:absolute;left:132px;top:25px;font-size:22px;color:var(--blue);font-weight:700}
.field{position:absolute;height:34px;background:var(--white);border:1px solid #c8c8c8;font-size:12px;color:var(--muted);padding:8px 10px}
.field.select::after{content:"";position:absolute;right:10px;top:13px;border:5px solid transparent;border-top-color:#555}
.search .to{position:absolute;left:385px;top:125px;font-size:13px;color:var(--ink)}
.search-btn{position:absolute;left:940px;top:119px;width:125px;height:34px;background:var(--navy);color:var(--white);font-size:13px;font-weight:600;display:flex;align-items:center;justify-content:center;gap:8px}

/* Welcome */
.welcome{top:770px;height:260px}
.welcome h1{margin-top:40px;font-size:36px;font-weight:400;color:#333;letter-spacing:.5px}
.welcome .tag{font-size:13px;letter-spacing:6px;color:var(--muted);margin-top:14px}
.welcome p{width:940px;margin:16px auto 0;font-size:13px;line-height:22px;color:#555}

/* Featured */
.featured{top:1030px;height:379px;background:var(--grey-band)}
.featured h2{margin-top:26px;font-size:24px;font-weight:400;color:#333}
.rule{width:800px;height:1px;background:#c5c5c5;margin:10px auto 0}
.cards{position:absolute;left:135px;top:92px;display:flex;gap:36px}
.card{width:205px;text-align:left}
.card .photo{height:143px;border:3px solid var(--white);position:relative}
.price{position:absolute;left:40px;bottom:-3px;width:120px;height:24px;background:var(--blue);color:var(--white);font-size:12px;font-weight:600;text-align:center;line-height:24px}
.card h3{font-size:14px;font-weight:700;margin-top:8px}
.card .sub{font-size:12px;color:var(--muted)}
.card .btn-blue{display:block;margin-top:10px;height:34px;line-height:34px}

/* Explore */
.explore{top:1409px;height:433px;background:linear-gradient(180deg,#0f1c2e 0%,#1c3452 55%,#0c1624 100%);color:var(--white)}
.explore h2{margin-top:30px;font-size:30px;font-weight:700;letter-spacing:.5px}
.explore p{width:940px;margin:16px auto 0;font-size:13px;line-height:20px;color:#dfe6ef}
.pill{display:inline-block;margin-top:22px;border:2px solid var(--white);border-radius:24px;padding:9px 26px;font-size:13px;font-weight:700;background:rgba(26,115,201,.6)}
.places{position:absolute;top:282px;left:150px;width:900px;display:flex;justify-content:space-between}
.place{width:130px;text-align:center;font-size:12px;font-weight:600;line-height:16px}
.place .badge{width:84px;height:84px;margin:0 auto 10px;background:var(--white);border:3px solid var(--blue);display:flex;align-items:center;justify-content:center}
.place .badge span{display:block;width:54px;height:54px;background:var(--blue)}

/* Sold */
.sold{top:1842px;height:307px}
.sold-box{position:absolute;left:134px;top:45px;width:934px;height:235px;border:2px solid #cfcfcf;background:#fafafa}
.sold-tab{position:absolute;left:490px;top:36px;width:220px;height:34px;background:var(--blue);color:var(--white);font-weight:700;font-size:15px;line-height:34px;text-align:center}
.sold-row{position:absolute;left:20px;top:52px;display:flex;gap:30px}
.sold-item{width:206px}
.sold-item .photo{height:125px;position:relative}
.sold-item .plus{position:absolute;left:50%;bottom:-10px;transform:translateX(-50%);width:20px;height:20px;background:var(--white);color:var(--blue);font-weight:700;text-align:center;line-height:20px}
.sold-meta{display:flex;justify-content:space-between;font-size:11px;font-weight:700;padding:10px 2px 6px}
.sold-meta .amt{color:var(--blue)}
.sold-bar{height:22px;background:var(--blue);color:var(--white);font-size:12px;font-weight:700;text-align:center;line-height:22px}

/* Team */
.team{top:2149px;height:508px}
.heading-lined{display:flex;align-items:center;justify-content:center;gap:16px;margin-top:44px;font-size:24px;font-weight:700;color:#333}
.heading-lined::before,.heading-lined::after{content:"";width:180px;height:1px;background:#bdbdbd}
.bubble{position:absolute;width:370px;background:var(--white);border:1px solid #cfcfcf;border-radius:18px;padding:26px;font-size:12px;line-height:20px;color:#555;box-shadow:0 2px 6px rgba(0,0,0,.08)}
.bubble::after{content:"";position:absolute;bottom:-14px;left:110px;width:24px;height:24px;background:var(--white);border-right:1px solid #cfcfcf;border-bottom:1px solid #cfcfcf;transform:rotate(45deg)}
.member{position:absolute;display:flex;align-items:center;gap:16px}
.avatar{width:92px;height:92px;border-radius:50%;border:4px solid #ddd;background:linear-gradient(135deg,#b9c7d6,#6f8598)}
.member .name{font-size:17px;font-weight:700}
.member .role{font-size:12px;font-style:italic;color:var(--muted)}

/* Consult */
.consult{top:2657px;height:313px;background:linear-gradient(90deg,#e5ecf3,#b9cadb)}
.consult-photo{position:absolute;right:0;top:0;width:620px;height:313px;background:linear-gradient(135deg,#e9eef3 0%,#c7d3de 50%,#8ea4b8 100%)}
.consult-panel{position:absolute;left:0;top:0}
.consult-copy{position:absolute;left:150px;top:70px;width:340px;text-align:right;color:var(--white)}
.consult-copy h2{font-size:22px;font-weight:400}
.consult-copy h2 b{font-weight:700}
.consult-copy p{margin-top:12px;font-size:13px;line-height:22px;font-weight:600}
.mail{position:absolute;left:515px;top:112px;width:62px;height:62px;border-radius:50%;background:var(--mail-grey);display:flex;align-items:center;justify-content:center}
.form{position:absolute;left:680px;top:22px;width:310px}
.form .in{height:38px;margin-bottom:10px;background:rgba(255,255,255,.25);border:1px solid rgba(255,255,255,.85);color:var(--white);font-size:13px;padding:9px 12px}
.form .in.msg{height:56px}
.form .send{margin-left:100px;width:100px;height:34px;line-height:34px;background:var(--blue);color:var(--white);font-weight:700;text-align:center;font-size:14px}

/* Blog */
.blog{top:2970px;height:508px}
.blog h2{margin-top:42px;font-size:24px;font-weight:700;color:#333}
.posts{position:absolute;left:135px;top:120px;display:flex;gap:55px;text-align:left}
.post{width:300px;position:relative}
.post .photo{margin-left:45px;height:185px}
.date{position:absolute;left:0;top:0;width:45px;height:75px;background:var(--blue);color:var(--white);text-align:center;font-weight:700}
.date .m{font-size:12px;padding-top:8px}
.date .d{font-size:20px}
.side-icon{position:absolute;left:0;width:45px;height:50px;background:#3a3a3a;display:flex;align-items:center;justify-content:center}
.post h3{margin:14px 0 0 45px;font-size:14px;font-weight:700}
.post .meta{margin-left:45px;font-size:10px;color:var(--muted);margin-top:4px}
.post p{margin:6px 0 0 45px;font-size:12px;line-height:18px;color:#555}
.post .btn-blue{margin:10px 0 0 45px;width:100px;height:28px;line-height:28px;border-radius:14px;font-size:12px}

/* Footer */
.footer{top:3478px;height:307px;background:var(--footer);color:var(--white)}
.footer h4{font-size:15px;font-weight:700}
.links{position:absolute;left:133px;top:40px}
.links .cols{display:flex;gap:70px;margin-top:22px;font-size:13px;line-height:26px;color:#cfcfcf}
.links .cols span::before{content:"› ";color:#888}
.follow{display:flex;align-items:center;gap:10px;margin-top:18px;font-size:14px;font-weight:700}
.follow .social{width:26px;height:26px;background:#333;border:none}
.video-col{position:absolute;left:440px;top:-16px;width:320px;height:323px;background:var(--footer-deep)}
.video-col h4{margin:40px 0 0 30px}
.video-thumb{position:absolute;left:30px;top:80px;width:260px;height:160px;background:linear-gradient(135deg,#8fb2cf,#e6e9ec 55%,#8a8d92)}
.video-bar{position:absolute;left:0;bottom:0;width:100%;height:22px;background:rgba(0,0,0,.7)}
.newsletter{position:absolute;left:815px;top:40px;width:255px}
.newsletter p{margin-top:20px;font-size:12px;line-height:20px;color:#cfcfcf}
.signup{display:flex;margin-top:14px}
.signup .mailbox{flex:1;height:34px;background:var(--white);color:var(--muted);font-size:12px;padding:9px 10px}
.signup .go{width:40px;height:34px;background:var(--blue);font-weight:700;text-align:center;line-height:34px}
.copyright{top:3785px;height:36px;background:var(--footer-deep);color:#aaa;font-size:12px;text-align:center;line-height:36px}
</style>
</head>
<body>

<header class="section hero">
  <div class="hero-photo" role="img" aria-label="Photograph of a luxury oceanfront estate with palm trees, lawn and a white pergola"></div>
  <div class="brand">Marwick on the Shore</div>
  <div class="topbar">
    <span class="social"></span><span class="social"></span><span class="social"></span><span class="social"></span>
    <span class="lang">English ▾</span>
  </div>
  <nav class="nav">
    <a class="active">Home</a><a>About us</a><a>Property Search</a><a>Team</a><a>Videos</a><a>Blog</a><a>Explore O.C</a><a>Contact</a>
  </nav>
  <h1 class="hero-title">LOOKING FOR A LUXURIOUS &amp; BEAUTIFUL HOME</h1>
  <div class="hero-actions">
    <div class="hero-btn">SELL YOUR HOME
      <svg viewBox="0 0 30 30"><circle cx="15" cy="15" r="13" fill="none" stroke="#fff" stroke-width="2"/><path d="M12 9l6 6-6 6" fill="none" stroke="#fff" stroke-width="2.5"/></svg></div>
    <div class="hero-btn">BUY YOUR HOME
      <svg viewBox="0 0 30 30"><circle cx="15" cy="15" r="13" fill="none" stroke="#fff" stroke-width="2"/><path d="M12 9l6 6-6 6" fill="none" stroke="#fff" stroke-width="2.5"/></svg></div>
  </div>
</header>

<section class="section search">
  <h2>Search Commercial REAl ESTATE LISTINGS</h2>
  <div class="field select" style="left:132px;top:70px;width:312px">Property Type</div>
  <div class="field" style="left:555px;top:70px;width:370px">Type Location or Project or Keyword</div>
  <div class="field select" style="left:132px;top:119px;width:235px">Min Price</div>
  <span class="to">To</span>
  <div class="field select" style="left:415px;top:119px;width:235px">Min Price</div>
  <div class="field select" style="left:675px;top:119px;width:250px">Posted by: All</div>
  <div class="search-btn">Search
    <svg width="14" height="14" viewBox="0 0 14 14"><circle cx="6" cy="6" r="4.5" fill="none" stroke="#fff" stroke-width="2"/><path d="M9.5 9.5L13 13" stroke="#fff" stroke-width="2"/></svg></div>
</section>

<section class="section welcome center">
  <h1>WELCOME TO MARWICK</h1>
  <div class="tag">ON THE SHORE</div>
  <p>We guide buyers and sellers of distinguished oceanfront homes along the Orange County coast. Our team pairs deep local knowledge with discreet, tailored service, so every showing, offer and closing feels calm and well planned. From quiet bluff-top villas to bright beachside retreats, we match each client with a home that suits the way they want to live by the water, and we stay beside them long after the keys change hands.</p>
</section>

<section class="section featured center">
  <h2>Featured Listings</h2>
  <div class="rule"></div>
  <div class="cards">
    <article class="card">
      <div class="photo" role="img" aria-label="Photograph of a beachfront home with palm trees and a pool" style="background:linear-gradient(160deg,#7fb4dc,#c9b48a 60%,#3f7a5a)"><span class="price">$ 1,495,000</span></div>
      <h3>14200 Ocean View</h3><div class="sub">Pacific Coast</div>
      <span class="btn-blue">View More</span>
    </article>
    <article class="card">
      <div class="photo" role="img" aria-label="Photograph of a modern villa at dusk with a lit pool" style="background:linear-gradient(160deg,#3d5f8e,#b07a4a 60%,#2d6f8f)"><span class="price">$ 1,495,000</span></div>
      <h3>Lorem ipsum dolor</h3><div class="sub">Pico Blvd</div>
      <span class="btn-blue">View More</span>
    </article>
    <article class="card">
      <div class="photo" role="img" aria-label="Photograph of a white coastal house on a lawn" style="background:linear-gradient(160deg,#9cc3e0,#e8e4da 55%,#6c9a4a)"><span class="price">$ 1,495,000</span></div>
      <h3>Lorem ipsum dolor</h3><div class="sub">Pico Blvd</div>
      <span class="btn-blue">View More</span>
    </article>
    <article class="card">
      <div class="photo" role="img" aria-label="Photograph of a contemporary home with warm interior lights" style="background:linear-gradient(160deg,#6f8fb0,#c08a5a 55%,#4a4a4a)"><span class="price">$ 1,495,000</span></div>
      <h3>Lorem ipsum dolor</h3><div class="sub">Pico Blvd</div>
      <span class="btn-blue">View More</span>
    </article>
  </div>
</section>

<section class="section explore center" role="img" aria-label="Night view of the Orange County coastline behind the section">
  <h2>EXPLORE ORANGE COUNTY</h2>
  <p>Sunlit beaches, quiet coves, lively harbors and family favorites sit within a short drive of every home we list. Spend a morning on the sand, an afternoon at a park or museum and an evening over dinner by the water. Discover the places our clients love most across the county.</p>
  <span class="pill">EXPLORE MORE</span>
  <div class="places">
    <div class="place"><div class="badge" role="img" aria-label="Farm illustration"><span></span></div>Harvest Berry Farm</div>
    <div class="place"><div class="badge" role="img" aria-label="Castle illustration"><span></span></div>Storybook Park</div>
    <div class="place"><div class="badge" role="img" aria-label="Stadium illustration"><span></span></div>Harbor Ballpark of Anaheim</div>
    <div class="place"><div class="badge" role="img" aria-label="Beach park illustration"><span></span></div>Coral Cove Shore Park</div>
    <div class="place"><div class="badge" role="img" aria-label="Zoo animal illustration"><span></span></div>Shoreline Family Zoo</div>
    <div class="place"><div class="badge" role="img" aria-label="Surfer illustration"><span></span></div>Coastal Surf History Museum</div>
  </div>
</section>

<section class="section sold">
  <div class="sold-box">
    <div class="sold-row">
      <div class="sold-item"><div class="photo" role="img" aria-label="Photograph of an ocean view deck" style="background:linear-gradient(160deg,#4f86b8,#9ab3c6 60%,#5a4a3a)"><span class="plus">+</span></div>
        <div class="sold-meta"><span>17410 Cypress ct12</span><span class="amt">$125548</span></div><div class="sold-bar">SOLD OUT</div></div>
      <div class="sold-item"><div class="photo" role="img" aria-label="Photograph of a pool courtyard" style="background:linear-gradient(160deg,#c8a878,#3fa6c8 60%,#6a8a4a)"><span class="plus">+</span></div>
        <div class="sold-meta"><span>17410 Cypress ct12</span><span class="amt">$125548</span></div><div class="sold-bar">SOLD OUT</div></div>
      <div class="sold-item"><div class="photo" role="img" aria-label="Photograph of a villa with palms" style="background:linear-gradient(160deg,#7aaed6,#d8c8a8 55%,#3b6a4a)"><span class="plus">+</span></div>
        <div class="sold-meta"><span>17410 Cypress ct12</span><span class="amt">$125548</span></div><div class="sold-bar">SOLD OUT</div></div>
      <div class="sold-item"><div class="photo" role="img" aria-label="Photograph of a terrace above the sea" style="background:linear-gradient(160deg,#9ec6e4,#f0ece4 55%,#4a86b0)"><span class="plus">+</span></div>
        <div class="sold-meta"><span>17410 Cypress ct12</span><span class="amt">$125548</span></div><div class="sold-bar">SOLD OUT</div></div>
    </div>
  </div>
  <div class="sold-tab">SOLD PROPERTIES</div>
</section>

<section class="section team">
  <h2 class="heading-lined">OUR TEAM</h2>
  <div class="bubble" style="left:220px;top:120px">Lena brings twenty years of coastal sales to every client. She knows each street and bluff along the shore and handles every deal with care, clear advice and quiet confidence from first visit to final close.</div>
  <div class="bubble" style="left:610px;top:100px">Theo leads our buyer services and market research. He studies every listing closely, guides clients through each offer and keeps the process calm, fast and well informed.</div>
  <div class="member" style="left:305px;top:340px"><div class="avatar" role="img" aria-label="Portrait of Lena Marwick"></div><div><div class="name">LENA MARWICK</div><div class="role">- Lorem ipsum Dolor</div></div></div>
  <div class="member" style="left:655px;top:318px"><div class="avatar" role="img" aria-label="Portrait of Theo"></div><div><div class="name">THEO</div><div class="role">- Lorem ipsum Dolor</div></div></div>
</section>

<section class="section consult">
  <div class="consult-photo" role="img" aria-label="Photograph of a smiling client advisor"></div>
  <svg class="consult-panel" width="720" height="313" viewBox="0 0 720 313"><polygon points="0,0 720,0 560,313 0,313" fill="#1a73c9" opacity=".92"/></svg>
  <div class="consult-copy">
    <h2><b>REQUEST</b> A CONSULT</h2>
    <p>GET STARTED BY FILLING OUT OUR ONLINE ENQUIRY FORM. WE'LL GET IN TOUCH WITHIN <b>24 HOURS</b></p>
  </div>
  <div class="mail"><svg width="28" height="20" viewBox="0 0 28 20"><rect x="1" y="1" width="26" height="18" fill="#fff"/><path d="M1 1l13 10L27 1" fill="none" stroke="#7a7a7a" stroke-width="2"/></svg></div>
  <div class="form">
    <div class="in">Name</div>
    <div class="in">Email</div>
    <div class="in">Phone Number</div>
    <div class="in msg">Your Message</div>
    <div class="send">Send</div>
  </div>
</section>

<section class="section blog center">
  <h2>LATEST FROM BLOG</h2>
  <div class="posts">
    <article class="post">
      <div class="date"><div class="m">FEB</div><div class="d">28</div></div>
      <div class="side-icon" style="top:75px"><svg width="16" height="14" viewBox="0 0 16 14"><path d="M8 13L1.5 6.5A3.5 3.5 0 018 2a3.5 3.5 0 016.5 4.5z" fill="#fff"/></svg></div>
      <div class="side-icon" style="top:125px"><svg width="16" height="14" viewBox="0 0 16 14"><path d="M1 1h14v9H6l-4 3V10H1z" fill="#fff"/></svg></div>
      <div class="photo" role="img" aria-label="Photograph of a living room with ocean view" style="background:linear-gradient(160deg,#d8d4cc,#6c88a4 55%,#2b2b2b)"></div>
      <h3>benefits of a reputable cabinet,</h3>
      <div class="meta">MAY 05, 2014 | 3 COMMENTS | ♥ 5</div>
      <p>Lorem ipsum dolor sit amet, consectetur adipiscing elit, sed diam nonummy nibh euismod tincidunt ut.</p>
      <span class="btn-blue">Read More</span>
    </article>
    <article class="post">
      <div class="date"><div class="m">FEB</div><div class="d">26</div></div>
      <div class="side-icon" style="top:75px"><svg width="16" height="14" viewBox="0 0 16 14"><path d="M8 13L1.5 6.5A3.5 3.5 0 018 2a3.5 3.5 0 016.5 4.5z" fill="#fff"/></svg></div>
      <div class="side-icon" style="top:125px"><svg width="16" height="14" viewBox="0 0 16 14"><path d="M1 1h14v9H6l-4 3V10H1z" fill="#fff"/></svg></div>
      <div class="photo" role="img" aria-label="Photograph of a villa terrace at sunset" style="background:linear-gradient(160deg,#f0b070,#8a6a5a 55%,#2a3a4a)"></div>
      <h3>benefits of a reputable cabinet,</h3>
      <div class="meta">MAY 05, 2014 | 3 COMMENTS | ♥ 5</div>
      <p>Lorem ipsum dolor sit amet, consectetur adipiscing elit, sed diam nonummy nibh euismod tincidunt ut.</p>
      <span class="btn-blue">Read More</span>
    </article>
    <article class="post">
      <div class="date"><div class="m">FEB</div><div class="d">25</div></div>
      <div class="side-icon" style="top:75px"><svg width="16" height="14" viewBox="0 0 16 14"><path d="M8 13L1.5 6.5A3.5 3.5 0 018 2a3.5 3.5 0 016.5 4.5z" fill="#fff"/></svg></div>
      <div class="side-icon" style="top:125px"><svg width="16" height="14" viewBox="0 0 16 14"><path d="M1 1h14v9H6l-4 3V10H1z" fill="#fff"/></svg></div>
      <div class="photo" role="img" aria-label="Photograph of a clifftop home at dusk" style="background:linear-gradient(160deg,#3a5a8a,#c89a6a 55%,#1e2e3e)"></div>
      <h3>benefits of a reputable cabinet,</h3>
      <div class="meta">MAY 05, 2014 | 3 COMMENTS | ♥ 5</div>
      <p>Lorem ipsum dolor sit amet, consectetur adipiscing elit, sed diam nonummy nibh euismod tincidunt ut.</p>
      <span class="btn-blue">Read More</span>
    </article>
  </div>
</section>

<footer class="section footer">
  <div class="links">
    <h4>Quick Links</h4>
    <div class="cols">
      <div><span>Home</span><br><span>About</span><br><span>Property Search</span><br><span>Explore O.C</span></div>
      <div><span>Team</span><br><span>Videos</span><br><span>Blog</span><br><span>Contact</span></div>
    </div>
    <div class="follow">Follow Us On <span class="social"></span><span class="social"></span><span class="social"></span><span class="social"></span></div>
  </div>
  <div class="video-col">
    <h4>Our Video</h4>
    <div class="video-thumb" role="img" aria-label="Video still of an oceanfront home">
      <svg style="position:absolute;left:110px;top:55px" width="40" height="30" viewBox="0 0 40 30"><rect width="40" height="30" rx="5" fill="#111"/><path d="M16 9l10 6-10 6z" fill="#fff"/></svg>
      <div class="video-bar"></div>
    </div>
  </div>
  <div class="newsletter">
    <h4>Newsletter Signup</h4>
    <p>Join our list for new listings, market notes and quiet previews of homes along the shore.</p>
    <div class="signup"><div class="mailbox">✉ Email Address</div><div class="go">GO</div></div>
  </div>
</footer>
<div class="section copyright">© 2015 Marwick on the Shore. All Rights Reserved.</div>

</body>
</html>
```